Business Card for beauty technology startup

Design Glimora Business Card for a Beauty, based on the website identity and colors (https://www.glimora-example.com).
Glimora is a beauty tech startup that gathers helpful product info for beauty lovers and consumers (such as availability on stores, price range and product reviews) for makeup products. The card design must be young, colorful but clean, and very modern.

Target Market(s)

woman, 15-35

Industry/Entity Type

Cosmetics

Contact Information for Business Card

Full Name, address, phone

Font styles to use
Other font styles liked:
• Advent Pro

Colors
e34297
86cfc6
ffffff
5c5c5c
e8e8e8
e667a6
b2b2b2

Requirements
Must have
• One full colored side with a creative design and another with card info
• Use Color palette: #95C5C5 and/or #D38AA5
• Use fonts: Advent Pro
• Use website identity: https://www.glimora-example.com
Nice to have
• If needed extra font: Roboto

```html
<!DOCTYPE html>
<html lang="en">
<head>
<meta charset="utf-8">
<title>Glimora Business Card</title>
<link rel="stylesheet" href="https://fonts.googleapis.com/css2?family=Advent+Pro:wght@300;400&family=Roboto:wght@400;500&display=swap">
<style>
  :root {
    --rose: #b97d95;
    --rose-soft: #c58ea4;
    --paper: #f6f6f6;
    --silver: #b2b2b2;
    --stage: #e8e8e8;
    --ink-light: #ffffff;
  }
  * { box-sizing: border-box; margin: 0; padding: 0; }
  html, body { width: 1200px; height: 886px; overflow: hidden; }
  body {
    background: var(--stage);
    position: relative;
    font-family: "Roboto", Arial, sans-serif;
  }
  .card {
    position: absolute;
    left: 270px;
    width: 660px;
    height: 377px;
    border-radius: 22px;
    overflow: hidden;
    box-shadow: 0 6px 18px rgba(0,0,0,0.15);
  }
  .card--back { top: 48px; background: var(--rose); }
  .card--front { top: 461px; background: var(--paper); }

  .back-circle {
    position: absolute;
    left: 40px; top: 40px;
    width: 300px; height: 300px;
    border-radius: 50%;
    border: 6px solid var(--rose-soft);
  }
  .back-brand {
    position: absolute;
    right: 44px; bottom: 58px;
    text-align: left;
    color: var(--ink-light);
  }
  .back-brand__name {
    font-family: "Advent Pro", "Roboto", sans-serif;
    font-weight: 300;
    font-size: 50px;
    letter-spacing: 9px;
    line-height: 1;
  }
  .back-brand__url {
    font-family: "Roboto", Arial, sans-serif;
    font-size: 13px;
    letter-spacing: 4.5px;
    margin-top: 4px;
  }

  .front-logo {
    position: absolute;
    left: 44px; top: 40px;
    display: flex; flex-direction: column; align-items: flex-start; gap: 18px;
  }
  .front-logo__mark {
    width: 72px; height: 72px;
    border-radius: 50%;
    border: 3px solid var(--rose);
    margin-left: 40px;
  }
  .front-logo__name {
    font-family: "Advent Pro", "Roboto", sans-serif;
    font-weight: 300;
    font-size: 46px;
    letter-spacing: 8px;
    color: var(--rose);
    line-height: 1;
  }
  .wave { position: absolute; inset: 0; width: 660px; height: 377px; }

  .contact {
    position: absolute;
    right: 40px; top: 150px;
    text-align: right;
    color: var(--ink-light);
    font-size: 15px;
    line-height: 1.25;
  }
  .contact__name { font-weight: 500; font-size: 19px; letter-spacing: 0.5px; }
  .contact__role { font-weight: 500; font-size: 15px; margin-bottom: 10px; }
  .contact__address { margin-bottom: 10px; }
  .contact__line { display: flex; justify-content: flex-end; align-items: center; gap: 8px; }
  .contact__icon { width: 14px; height: 14px; flex: none; }
</style>
</head>
<body>
  <section class="card card--back" aria-label="Card back">
    <div class="back-circle"></div>
    <div class="back-brand">
      <div class="back-brand__name">GLIMORA</div>
      <div class="back-brand__url">www.glimora-example.com</div>
    </div>
  </section>

  <section class="card card--front" aria-label="Card front">
    <svg class="wave" viewBox="0 0 660 377" aria-hidden="true">
      <path d="M0 330 C 150 340, 230 300, 330 220 C 430 140, 520 120, 660 135 L660 377 L0 377 Z" fill="var(--rose)"/>
      <path d="M40 322 C 170 325, 250 280, 340 205 C 430 130, 530 112, 640 125" fill="none" stroke="var(--silver)" stroke-width="5"/>
    </svg>

    <div class="front-logo">
      <div class="front-logo__mark"></div>
      <div class="front-logo__name">GLIMORA</div>
    </div>

    <div class="contact">
      <div class="contact__name">MARA ELLISON</div>
      <div class="contact__role">CEO/FOUNDER</div>
      <div class="contact__address">4120 Larkspur Court<br>Fairview, Oregon 97024</div>
      <div class="contact__line">555 014 2290
        <svg class="contact__icon" viewBox="0 0 14 14"><path d="M3 1 L5 4 L4 5.5 C5 8 6 9 8.5 10 L10 9 L13 11 L11.5 13 C6 12.5 1.5 8 1 2.5 Z" fill="#fff"/></svg>
      </div>
      <div class="contact__line">555 017 6843
        <svg class="contact__icon" viewBox="0 0 14 14"><rect x="3.5" y="1" width="7" height="12" rx="1.2" fill="none" stroke="#fff" stroke-width="1.4"/></svg>
      </div>
      <div class="contact__line">555 019 3071
        <svg class="contact__icon" viewBox="0 0 14 14"><rect x="4" y="1" width="6" height="4" fill="#fff"/><rect x="1" y="5" width="12" height="6" rx="1" fill="#fff"/><rect x="4" y="9" width="6" height="4" fill="#fff" stroke="var(--rose)" stroke-width="0.8"/></svg>
      </div>
      <div class="contact__line">info@glimora-example.com
        <svg class="contact__icon" viewBox="0 0 14 14"><rect x="1" y="3" width="12" height="8" fill="#fff"/><path d="M1 3 L7 8 L13 3" fill="none" stroke="var(--rose)" stroke-width="1"/></svg>
      </div>
      <div class="contact__line">www.glimora-example.com
        <svg class="contact__icon" viewBox="0 0 14 14"><circle cx="7" cy="7" r="6" fill="#fff"/><path d="M1 7 H13 M7 1 C4 4 4 10 7 13 M7 1 C10 4 10 10 7 13" fill="none" stroke="var(--rose)" stroke-width="0.9"/></svg>
      </div>
    </div>
  </section>
</body>
</html>
```